Brightvale cleaning and maintenance company

An expansive website whereby we can advertise our commercial cleaning and maintenance services across a service portfolio of commercial cleaning and property maintenance. Whereby potential skilled resources can deposit there resume so we can collaborate and match candidates to a broad range of cleaning and maintenance jobs/projects.
Updates

Looking for more extensive ideas so the front page can change pictures on it with the focus for Brightvale Commercial Cleaning and Maintenance. Also need to bring in all the portfolios we offer including 1. Equipment Cleaning and Sanitisation Services 2. High pressure gurney and play ground equipment cleaning 3. General Cleaning and Property Facilities Management 4. Project and Recruiting Services, to allow for potential professional cleaners, handy man, mechanics, warehousing resources , electricians to deposit there resume. Most of the designers have stuck with the old portfolio categories , however the portfolio of services we offer has been updated so that needs to be reflected in the website. Also not necessary to use all my original photos I would like the opening page of the website to perhaps be able to change and have different pictures is that possible thank you

```html
<!DOCTYPE html>
<html lang="en">
<head>
<meta charset="utf-8">
<title>Brightvale – Commercial Cleaning &amp; Maintenance</title>
<link rel="stylesheet" href="https://fonts.googleapis.com/css2?family=IBM+Plex+Sans:wght@400;500;600;700&family=Libre+Baskerville:wght@400;700&display=swap">
<style>
:root{
  --navy:#0f2a5c;
  --orange:#ef3e1f;
  --ink:#222222;
  --muted:#555555;
  --paper:#ffffff;
  --mist:#f1eff0;
  --rule:#c9c9c9;
  --charcoal:#252525;
  --social:#2f7fd8;
}
*{margin:0;padding:0;box-sizing:border-box}
html,body{width:1200px;height:4326px;overflow:hidden}
body{position:relative;background:var(--paper);font-family:"IBM Plex Sans",Arial,sans-serif;color:var(--ink)}
.serif{font-family:"Libre Baskerville",Georgia,serif}
section,header,footer,nav{position:absolute;left:0;width:1200px}
.abs{position:absolute}
.btn{position:absolute;display:flex;align-items:center;justify-content:center;background:var(--orange);color:#fff;font-weight:600;text-transform:uppercase;letter-spacing:.5px;white-space:nowrap}

/* header */
.site-header{top:0;height:92px;background:var(--paper)}
.brand{left:134px;top:22px;display:flex;align-items:center;gap:12px}
.brand-dot{width:46px;height:46px;border-radius:50%;background:var(--navy)}
.brand-name{font-family:"Libre Baskerville",Georgia,serif;font-size:37px;color:var(--orange)}
.follow{left:525px;top:30px;display:flex;align-items:center;gap:8px;font-size:12px;font-weight:600;color:var(--navy)}
.follow i{display:block;width:26px;height:26px;border-radius:50%;background:var(--social)}
.quote-top{left:698px;top:24px;width:126px;height:38px;border:2px solid var(--navy);color:var(--navy);font-size:13px;font-weight:700;display:flex;align-items:center;justify-content:center}
.call{left:852px;top:20px;display:flex;gap:14px;align-items:center}
.call small{display:block;font-size:12px;font-weight:600;color:var(--navy)}
.call strong{display:block;font-size:22px;font-weight:700;color:var(--orange);line-height:1.1}

/* nav */
.main-nav{top:92px;height:37px;background:var(--navy)}
.main-nav a{position:absolute;top:0;height:37px;line-height:37px;color:#fff;font-size:13.5px;font-weight:500;text-decoration:none;text-transform:uppercase}
.main-nav .active{background:var(--orange);padding:0 16px}

/* hero */
.hero{top:129px;height:534px;background:linear-gradient(115deg,#5b4a3e 0%,#7b6656 30%,#a56a44 45%,#6e5a4a 60%,#8a7a68 80%,#5a4c42 100%)}
.hero-title{left:671px;top:113px;font-size:54px;line-height:64px;color:#fff;font-weight:400}
.hero .btn{left:678px;top:274px;width:144px;height:47px;font-size:16px;border:2px solid #fff;box-shadow:0 0 0 1px var(--orange)}
.hero-arrow{top:246px;width:34px;height:34px;background:#fff;display:flex;align-items:center;justify-content:center}

/* section heading */
.sec-title{position:absolute;left:0;width:1200px;text-align:center;font-family:"Libre Baskerville",Georgia,serif;font-size:32px;color:var(--navy);font-weight:400}
.sec-rule{position:absolute;left:580px;width:40px;height:3px;background:#b5b5b5}

/* services */
.services{top:663px;height:874px}
.svc-card{position:absolute;width:456px;height:321px;overflow:hidden}
.svc-card .shade{position:absolute;left:0;right:0;bottom:0;height:55%;background:linear-gradient(to bottom,rgba(15,42,92,0),rgba(15,42,92,.85))}
.svc-label{position:absolute;left:23px;bottom:22px;width:270px;color:#fff;font-size:15px;font-weight:700;text-transform:uppercase;line-height:20px}
.svc-label:before{content:"";display:block;width:20px;height:2px;background:#fff;margin-bottom:10px}
.svc-card .btn{right:40px;bottom:26px;height:26px;padding:0 10px;font-size:11px}
.svc-hub{left:569px;top:445px;width:60px;height:60px;border-radius:50%;background:#fff}

/* working */
.working{top:1537px;height:500px;background:var(--mist)}
.work-photo{left:134px;top:32px;width:445px;height:440px;border-radius:46% 54% 50% 50%;background:radial-gradient(circle at 40% 40%,#e6edf3 0%,#b9c7d6 45%,#4a6ea8 75%,#1f3f7a 100%)}
.work-copy{left:659px;top:56px;width:400px}
.work-copy .kicker{font-family:"Libre Baskerville",Georgia,serif;font-size:22px;color:var(--navy)}
.work-copy .name{font-family:"Libre Baskerville",Georgia,serif;font-size:35px;color:var(--orange);margin-top:6px}
.work-copy h3{font-size:16px;font-weight:600;text-transform:uppercase;line-height:22px;margin-top:22px;color:#1c1c1c}
.work-copy p{font-size:14.5px;line-height:21px;color:#333;margin-top:16px}
.working .btn{left:661px;top:416px;width:114px;height:32px;font-size:14px}

/* values */
.values{top:2037px;height:769px}
.value-ring{left:250px;top:130px;width:700px;height:560px;border-radius:50%;background:#efefef}
.value-dot{position:absolute;width:116px;height:116px;border-radius:50%;background:var(--navy);display:flex;align-items:center;justify-content:center}
.value{position:absolute;width:240px}
.value h4{font-size:13.5px;font-weight:600;text-transform:uppercase;color:#222;letter-spacing:.3px}
.value p{font-size:12px;line-height:16px;color:var(--muted);margin-top:6px}
.value.right-al{text-align:right}
.value.center-al{text-align:center}

/* management */
.management{top:2806px;height:560px;background:var(--navy)}
.management .sec-title{color:#fff}
.mgmt-card{position:absolute;top:157px;width:223px;height:351px;background:#fff}
.mgmt-card h4{position:absolute;left:24px;top:22px;width:185px;font-size:15px;font-weight:700;text-transform:uppercase;color:var(--navy);line-height:18px}
.mgmt-card h4:after{content:"";display:block;width:52px;height:2px;background:var(--orange);margin-top:8px}
.mgmt-row{position:absolute;left:24px;width:185px;font-size:13.5px;line-height:19px;color:#444}
.mgmt-rule{position:absolute;left:14px;width:195px;height:1px;background:var(--rule)}
.mgmt-row b{font-weight:600;color:#222}
.mgmt-row small{font-size:11px;line-height:14px;display:block}

/* clients */
.clients{top:3366px;height:316px}
.client-row{position:absolute;left:133px;top:192px;width:934px;display:flex;justify-content:space-between;align-items:center}
.client{font-size:18px;font-weight:700;color:#2a2a2a;white-space:nowrap}

/* coverage */
.coverage{top:3682px;height:245px;background:var(--charcoal)}
.coverage p{position:absolute;left:0;top:55px;width:1200px;text-align:center;font-family:"Libre Baskerville",Georgia,serif;font-size:24px;line-height:34px;color:#fff}
.coverage .btn{left:532px;top:149px;width:138px;height:35px;font-size:16px}

/* footer */
.site-footer{top:3927px;height:399px;background:var(--mist)}
.foot-brand{left:134px;top:140px;display:flex;align-items:center;gap:14px}
.foot-brand i{display:block;width:52px;height:52px;border-radius:50%;background:var(--navy)}
.foot-brand span{font-family:"Libre Baskerville",Georgia,serif;font-size:34px;color:var(--navy)}
.foot-h{position:absolute;top:50px;font-size:14px;font-weight:700;color:var(--navy);text-transform:uppercase}
.foot-menu{position:absolute;left:438px;top:96px;list-style:none}
.foot-menu li{font-size:14px;line-height:24px;color:#333;text-transform:uppercase}
.foot-item{position:absolute;display:flex;align-items:flex-start;gap:14px;font-size:14px;line-height:20px;color:#333}
.foot-item .ico{flex:none;width:26px;height:26px;border-radius:50%;background:var(--navy);display:flex;align-items:center;justify-content:center;margin-top:4px}
.copyright{position:absolute;left:0;top:354px;width:1208px;text-align:center;font-size:11.5px;color:#444}
</style>
</head>
<body>

<header class="site-header">
  <div class="abs brand"><span class="brand-dot"></span><span class="brand-name">Brightvale</span></div>
  <div class="abs follow">FOLLOW US <i></i><i></i></div>
  <div class="abs quote-top">GET A QUOTE</div>
  <div class="abs call">
    <svg width="32" height="32" viewBox="0 0 24 24" fill="none" stroke="#0f2a5c" stroke-width="1.8"><path d="M5 3h4l2 5-2.5 1.5a11 11 0 0 0 6 6L16 13l5 2v4a2 2 0 0 1-2 2A16 16 0 0 1 3 5a2 2 0 0 1 2-2z"/><path d="M15 3a6 6 0 0 1 6 6M15 7a2 2 0 0 1 2 2"/></svg>
    <div><small>CALL US</small><strong>(07) 5550 0182</strong></div>
  </div>
</header>

<nav class="main-nav">
  <a class="active" style="left:131px">Home</a>
  <a style="left:257px">Services</a>
  <a style="left:404px">About Us</a>
  <a style="left:581px">Our People</a>
  <a style="left:750px">Safety &amp; Compliance</a>
  <a style="left:1002px">Contact</a>
</nav>

<section class="hero" role="img" aria-label="Photo: high pressure water jet cleaning a stained paved path">
  <h1 class="abs hero-title serif">High Pressure<br>Water Cleaning</h1>
  <span class="btn">Read More</span>
  <span class="abs hero-arrow" style="left:0"><svg width="12" height="16" viewBox="0 0 12 16"><path d="M9 2 3 8l6 6" fill="none" stroke="#222" stroke-width="2"/></svg></span>
  <span class="abs hero-arrow" style="left:1166px"><svg width="12" height="16" viewBox="0 0 12 16"><path d="m3 2 6 6-6 6" fill="none" stroke="#222" stroke-width="2"/></svg></span>
</section>

<section class="services">
  <h2 class="sec-title" style="top:46px">Our Services</h2>
  <span class="sec-rule" style="top:97px"></span>

  <article class="svc-card" style="left:133px;top:142px;background:linear-gradient(135deg,#3c3c40 0%,#6e6e72 40%,#d7849a 55%,#8a8a8e 70%,#2e2e32 100%)" role="img" aria-label="Photo: gloved hand wiping and sanitising the inside of a microwave oven">
    <span class="shade"></span>
    <div class="svc-label">Equipment Cleaning<br>&amp; Sanitisation</div>
    <span class="btn">Read More</span>
  </article>
  <article class="svc-card" style="left:609px;top:142px;background:linear-gradient(135deg,#5a7f3a 0%,#8a6fb0 35%,#d8443a 50%,#3f63a8 65%,#6b8a46 100%)" role="img" aria-label="Photo: playground swing and equipment">
    <span class="shade"></span>
    <div class="svc-label">High Pressure Gurney &amp;<br>Playground Cleaning</div>
    <span class="btn">Read More</span>
  </article>
  <article class="svc-card" style="left:133px;top:488px;background:linear-gradient(135deg,#9aa0a6 0%,#4a4e54 35%,#7e848a 60%,#33373c 100%)" role="img" aria-label="Photo: clean stainless steel commercial kitchen in a managed property">
    <span class="shade"></span>
    <div class="svc-label">General Cleaning &amp;<br>Facilities Management</div>
    <span class="btn">Read More</span>
  </article>
  <article class="svc-card" style="left:609px;top:488px;background:linear-gradient(135deg,#8c8a80 0%,#3d5688 30%,#9a6a44 55%,#b98a5e 80%,#7a5a3e 100%)" role="img" aria-label="Photo: tradesperson at work on a project site">
    <span class="shade"></span>
    <div class="svc-label">Project &amp;<br>Recruiting Services</div>
    <span class="btn">Send Resume</span>
  </article>
  <span class="abs svc-hub"></span>
</section>

<section class="working">
  <div class="abs work-photo" role="img" aria-label="Photo: cleaner in blue overalls mopping a bright office floor"></div>
  <div class="abs work-copy">
    <div class="kicker">Working with</div>
    <div class="name">Brightvale</div>
    <h3>We are Brightvale, a leading Australian cleaning services company.</h3>
    <p>When you work with Brightvale it is easy to do business with us. We have been in the equipment services industry for close to 15 years.</p>
    <p>Our people are professional, reliable and service oriented. In every interaction you have; on site, receiving help from our service support staff, or rolling-out new cleaning sites, you will see and feel the benefits of using Brightvale.</p>
  </div>
  <span class="btn">Read More</span>
</section>

<section class="values">
  <h2 class="sec-title" style="top:68px">We Value</h2>
  <span class="sec-rule" style="top:119px"></span>
  <span class="abs value-ring"></span>

  <span class="value-dot" style="left:449px;top:197px">
    <svg width="46" height="46" viewBox="0 0 24 24" fill="none" stroke="#fff" stroke-width="1.6"><path d="M12 2 4 5v6c0 5 3.5 9 8 11 4.5-2 8-6 8-11V5z"/><path d="m8 12 3 3 5-6"/></svg>
  </span>
  <span class="value-dot" style="left:630px;top:187px">
    <svg width="46" height="46" viewBox="0 0 24 24" fill="none" stroke="#fff" stroke-width="1.6"><circle cx="8" cy="12" r="4"/><circle cx="16" cy="12" r="4"/></svg>
  </span>
  <span class="value-dot" style="left:705px;top:358px">
    <svg width="46" height="46" viewBox="0 0 24 24" fill="none" stroke="#fff" stroke-width="1.6"><path d="m5 12 5 5 9-10"/></svg>
  </span>
  <span class="value-dot" style="left:410px;top:397px">
    <svg width="46" height="46" viewBox="0 0 24 24" fill="none" stroke="#fff" stroke-width="1.6"><circle cx="12" cy="12" r="3"/><circle cx="12" cy="12" r="7" stroke-dasharray="3 2.5"/></svg>
  </span>
  <span class="value-dot" style="left:570px;top:503px">
    <svg width="46" height="46" viewBox="0 0 24 24" fill="none" stroke="#fff" stroke-width="1.6"><path d="M20 12a8 8 0 1 1-3-6.2"/><path d="M17 2v4h4"/></svg>
  </span>

  <div class="value right-al" style="left:190px;top:223px"><h4>Safety and the Environment</h4><p>We are committed to providing a safe and healthy working environment;</p></div>
  <div class="value" style="left:765px;top:223px"><h4>Positive Working Relationships</h4><p>Having relationships that focus on shared goals and creation of value for all parties;</p></div>
  <div class="value" style="left:842px;top:392px;width:200px"><h4>Respect for Each Other</h4><p>The embracing of diversity, enriched by openness, sharing, trust, teamwork and involvement.</p></div>
  <div class="value right-al" style="left:148px;top:431px;width:240px"><h4>Professionalism/Integrity</h4><p>We are committed to doing what we<br>say we are going to do</p></div>
  <div class="value center-al" style="left:488px;top:624px;width:270px"><h4>Sustainability</h4><p>Achieving results that are mutually beneficial for our employees, our customers, our partners and the company;</p></div>
</section>

<section class="management">
  <h2 class="sec-title" style="top:50px">Service Management</h2>
  <span class="sec-rule" style="top:101px;background:#8f9bb3"></span>

  <div class="mgmt-card" style="left:133px">
    <h4>Office Hours</h4>
    <div class="mgmt-row" style="top:113px">Weekdays<br>(Monday–Friday)</div>
    <span class="mgmt-rule" style="top:160px"></span>
    <div class="mgmt-row" style="top:183px">Weekdays<br>(Saturday &amp; Sunday)</div>
    <span class="mgmt-rule" style="top:231px"></span>
    <div class="mgmt-row" style="top:257px">Public Holidays</div>
  </div>
  <div class="mgmt-card" style="left:372px">
    <h4>Normal Business Hours</h4>
    <div class="mgmt-row" style="top:113px">Head Office</div>
    <span class="mgmt-rule" style="top:160px"></span>
    <div class="mgmt-row" style="top:183px">8am — 5pm N/A</div>
    <span class="mgmt-rule" style="top:231px"></span>
    <div class="mgmt-row" style="top:257px">Yes, for rostered<br>services</div>
  </div>
  <div class="mgmt-card" style="left:612px">
    <h4>Capability to deliver at short notice response time</h4>
    <div class="mgmt-row" style="top:113px">within 24 hours</div>
    <span class="mgmt-rule" style="top:160px"></span>
    <div class="mgmt-row" style="top:183px">within 24 hours</div>
    <span class="mgmt-rule" style="top:231px"></span>
    <div class="mgmt-row" style="top:257px">within 24 hours</div>
  </div>
  <div class="mgmt-card" style="left:851px">
    <h4>Costings</h4>
    <div class="mgmt-row" style="top:105px">Call out fee<br><b>$ 40.00 + GST</b></div>
    <span class="mgmt-rule" style="top:160px"></span>
    <div class="mgmt-row" style="top:182px">Call out fee<br><b>$ 40.00 + GST</b></div>
    <span class="mgmt-rule" style="top:231px"></span>
    <div class="mgmt-row" style="top:252px">Public Holiday fee<br><b>$ 50.00 + GST</b><small>(single unit machine)</small><b>$ 75.00 + GST</b><small>(double unit machine)</small></div>
  </div>
</section>

<section class="clients">
  <h2 class="sec-title" style="top:66px">Our Clients</h2>
  <span class="sec-rule" style="top:116px"></span>
  <div class="client-row">
    <span class="client">Harbor Grill</span>
    <span class="client">Sunrise Diner</span>
    <span class="client">Crestline Drinks</span>
    <span class="client">Patty Barn</span>
    <span class="client">Ledgerwood</span>
    <span class="client">Ovenworks</span>
  </div>
</section>

<section class="coverage">
  <p>Servicing Metropolitan Sydney, Brisbane, Melbourne,<br>Adelaide, Newcastle and Regional areas as required.</p>
  <span class="btn">Get a Quote</span>
</section>

<footer class="site-footer">
  <div class="abs foot-brand"><i></i><span>Brightvale</span></div>

  <div class="foot-h" style="left:438px">Menu</div>
  <ul class="foot-menu">
    <li>Home</li><li>Services</li><li>About Us</li><li>Our People</li><li>Safety &amp; Compliance</li><li>Contact</li>
  </ul>

  <div class="foot-h" style="left:670px">Contact Us</div>
  <div class="foot-item" style="left:668px;top:96px">
    <span class="ico"><svg width="12" height="14" viewBox="0 0 12 14"><path d="M6 1a4 4 0 0 0-4 4c0 3 4 8 4 8s4-5 4-8a4 4 0 0 0-4-4z" fill="#fff"/><circle cx="6" cy="5" r="1.4" fill="#0f2a5c"/></svg></span>
    <span>2150 Harbour Street<br>Sunnyvale Bay 4217</span>
  </div>
  <div class="foot-item" style="left:668px;top:158px">
    <span class="ico"><svg width="13" height="13" viewBox="0 0 24 24"><path d="M5 3h4l2 5-2.5 1.5a11 11 0 0 0 6 6L16 13l5 2v4a2 2 0 0 1-2 2A16 16 0 0 1 3 5a2 2 0 0 1 2-2z" fill="#fff"/></svg></span>
    <span>Call Us<br>(07) 5550 0182</span>
  </div>
  <div class="foot-item" style="left:668px;top:220px">
    <span class="ico"><svg width="13" height="10" viewBox="0 0 13 10"><rect x=".5" y=".5" width="12" height="9" fill="#fff"/><path d="m1 1 5.5 4.5L12 1" fill="none" stroke="#0f2a5c"/></svg></span>
    <span>E mail Us<br>info@brightvale.example</span>
  </div>

  <div class="foot-h" style="left:948px">Follow Us</div>
  <div class="foot-item" style="left:946px;top:96px"><span class="ico"></span><span>Like us on<br>FRIENDLINK</span></div>
  <div class="foot-item" style="left:946px;top:158px"><span class="ico"></span><span>Follow us on<br>CHIRPER</span></div>
  <div class="foot-item" style="left:946px;top:220px"><span class="ico"></span><span>Follow us on<br>WORKLINE</span></div>

  <div class="copyright">Copyright © 2020 All Rights Reserved</div>
</footer>

</body>
</html>
```